Health Coaching website focused on diabetes management using Vantelo template

I am starting a health coaching business and would like to use Plumestack and an Vantelo template. The coaching will focus on Pre-diabetic and chronic disease patients so it will need to have a personal as well as a slight clinical look to it. The site should have an overall look similar to Meadow Loop theme. I will purchase the Vantelo designer package for use.

Target Market(s)

40-60 year olds with pre-diabetes or concerned about chronic disease, maintaining health, nutrition and weight loss

Industry/Entity Type

Health And Wellness

Number of Pages Required

5+ page

Colors
87cfc6
60b9df
fee18a
00a990
3276b5

Requirements
Must have
• It should contain an ecommerce tab, member's only area, interactive blog, built-in SEO and an opt-in area on every page. It should have several call to actions throughout the site. The site should have an overall look similar to Meadow Loop theme. Hosting on Servunda. Also needed all the essential plumestack plugins:
• Keystep forms & Keystep entry pages
• Pondra Metrics
• Vantelo shield plus
• Postwren
• Valdeno
• Vault Parrot
• Kindle SEO
• Drifting Share Strip
• Q7 Rapid Store
• Tembi
Nice to have
• Ecommerce ready with cartoflex plugin
• Hi-res pictures of people in my demographic enjoying life and/or exercising, cooking, etc.
Should not have
• slider on homepage
• my profile on homepage

```html
<!DOCTYPE html>
<html lang="en">
<head>
<meta charset="utf-8">
<title>VitalPath For Wellness — Testimonials</title>
<link rel="stylesheet" href="https://fonts.googleapis.com/css2?family=Jost:wght@300;400&family=Open+Sans:ital,wght@0,400;0,600;0,700;1,400&display=swap">
<style>
:root{
  --teal:#00a990;
  --teal-dark:#008f7a;
  --blue:#3276b5;
  --blue-light:#60b9df;
  --mint:#87cfc6;
  --ink:#1d1d1d;
  --text:#333;
  --rule:#d9d9d9;
  --crumb:#e8e8e8;
  --footer:#1e242d;
  --footer-text:#c7ccd2;
  --quote:#a9c6e3;
}
*{box-sizing:border-box;margin:0;padding:0}
html,body{width:975px;height:1200px;overflow:hidden;background:#fff}
body{position:relative;font-family:"Open Sans",sans-serif;color:var(--text)}
.abs{position:absolute}

/* header */
.brand{left:131px;top:14px;display:flex;align-items:center;gap:10px}
.brand-dot{width:58px;height:58px;border-radius:50%;background:var(--mint)}
.brand-name{font-family:"Jost",sans-serif;font-weight:300;font-size:27px;line-height:30px;color:#333}
.phone{left:508px;top:33px;display:flex;align-items:center;gap:10px;font-size:17px;color:#444}
.phone-icon{width:30px;height:30px;border-radius:50%;background:var(--teal);display:flex;align-items:center;justify-content:center}
.cta{left:667px;top:32px;width:177px;height:31px;background:var(--teal);border-bottom:2px solid var(--teal-dark);color:#fff;font-size:11px;display:flex;align-items:center;justify-content:center;gap:8px;letter-spacing:.2px}

/* nav */
.navbar{left:0;top:92px;width:975px;height:30px;background:var(--blue)}
.nav{left:131px;top:92px;height:30px;display:flex;border-left:1px solid #2a66a0}
.nav a{display:flex;align-items:center;justify-content:center;height:30px;color:#fff;font-size:10px;font-weight:700;text-decoration:none;border-right:1px solid #2a66a0}
.nav a.active{background:var(--teal)}

/* hero */
.hero{left:0;top:122px;width:975px;height:274px;background:#eeebe2}
.hero-photo{left:0;top:122px;width:540px;height:274px;background:linear-gradient(90deg,#8a5a36 0%,#c39068 30%,#d9c7ad 70%,#eeebe2 100%)}
.hero-title{left:560px;top:168px;width:275px;text-align:center;font-family:"Jost",sans-serif;font-weight:400;font-size:41px;line-height:50px;color:#111}
.hero-sub{left:560px;top:274px;width:275px;text-align:center;font-size:15px;line-height:18px;color:#111}
.dots{left:675px;top:339px;display:flex;gap:5px}
.dots span{width:8px;height:8px;border-radius:50%;background:#555}
.dots span.on{width:10px;height:10px;margin-top:-1px;background:var(--teal)}

/* breadcrumb */
.crumbbar{left:0;top:396px;width:975px;height:31px;background:var(--crumb)}
.crumb{left:131px;top:405px;font-size:10px;color:#333}
.crumb b{font-weight:700}

/* section title */
.section-title{left:0;top:455px;width:975px;text-align:center;font-family:"Jost",sans-serif;font-weight:300;font-size:28px;color:#222}
.section-title span{color:var(--blue)}
.divider{left:297px;top:509px;width:382px;height:1px;background:#aaa}
.divider-mark{left:478px;top:501px;width:18px;height:18px;border-radius:50%;background:#fff;border:1px solid #aaa}

/* testimonials */
.avatar{width:75px;height:75px;border-radius:50%;border:2px solid var(--teal);background:radial-gradient(circle at 50% 40%,#c9a088,#6e5a4e)}
.avatar-tail{width:0;height:0;border-left:8px solid transparent;border-right:4px solid transparent;border-top:10px solid var(--teal)}
.quote{left:217px;width:627px;font-style:italic;font-size:10px;line-height:15.5px;color:#222;text-indent:18px}
.qmark{font-family:Georgia,serif;font-size:26px;line-height:1;color:var(--quote);font-style:normal;font-weight:700}
.qopen{left:217px}
.body{left:217px;width:627px;font-size:10.3px;line-height:15.6px;color:#333;text-align:justify}
.short-rule{left:220px;width:240px;height:1px;background:linear-gradient(90deg,#ccc,#fff)}
.author{left:221px;font-size:10.3px;font-weight:700;color:#222}
.sep{left:131px;width:714px;height:1px;background:var(--rule)}

/* footer */
.footer{left:0;top:936px;width:975px;height:227px;background:var(--footer)}
.f-head{font-family:"Jost",sans-serif;font-size:15px;color:#fff;letter-spacing:.2px}
.f-head span{color:var(--teal)}
.f-rule{height:1px;background:#4a525c}
.links{left:131px;top:1009px;list-style:none;font-size:10px;line-height:16.4px;color:var(--footer-text)}
.links li::before{content:"›";color:var(--teal);margin-right:6px}
.links li.current{color:var(--teal)}
.contact{left:265px;top:1010px;font-size:10px;color:var(--footer-text);line-height:14.5px}
.contact .org{color:#fff;margin-bottom:2px}
.c-row{display:flex;align-items:center;gap:8px;margin-top:8px;font-size:13px}
.c-row.small{font-size:10px;margin-top:12px}
.social{left:467px;list-style:none;font-size:10px;color:var(--footer-text)}
.social li{display:flex;align-items:center;gap:10px;height:25px;margin-bottom:6px}
.social i{width:25px;height:25px;border-radius:50%;border:2px solid #fff;background:var(--blue)}
.social li.red i{background:#c8232c}
.footer-mark{left:690px;top:980px;width:150px;height:150px;border-radius:50%;background:#3a414b}
.bottom{left:0;top:1163px;width:975px;height:37px;background:var(--teal);color:#fff;font-size:10px;padding:15px 0 0 132px}
</style>
</head>
<body>

<!-- header -->
<div class="abs brand">
  <div class="brand-dot"></div>
  <div class="brand-name">VitalPath<br>For Wellness</div>
</div>
<div class="abs phone">
  <div class="phone-icon">
    <svg width="14" height="14" viewBox="0 0 24 24"><path fill="#fff" d="M6.6 10.8a15 15 0 0 0 6.6 6.6l2.2-2.2c.3-.3.7-.4 1-.2 1.1.4 2.3.6 3.6.6.6 0 1 .4 1 1V20c0 .6-.4 1-1 1A17 17 0 0 1 3 4c0-.6.4-1 1-1h3.5c.6 0 1 .4 1 1 0 1.3.2 2.5.6 3.6.1.3 0 .7-.2 1z"/></svg>
  </div>
  312-555-0148
</div>
<div class="abs cta">
  <svg width="13" height="13" viewBox="0 0 14 14"><rect x="1" y="2.5" width="12" height="10.5" fill="none" stroke="#fff" stroke-width="1.2"/><path d="M1 5.5h12M4 1v3M10 1v3" stroke="#fff" stroke-width="1.2"/><path d="M3.5 7.5h1.5M6.3 7.5h1.5M9 7.5h1.5M3.5 10h1.5M6.3 10h1.5M9 10h1.5" stroke="#fff"/></svg>
  MAKE AN APPOINTMENT
</div>

<!-- navigation -->
<div class="abs navbar"></div>
<nav class="abs nav">
  <a style="width:58px">HOME</a>
  <a style="width:144px">ABOUT VITALPATH</a>
  <a style="width:100px">OUR COURSES</a>
  <a style="width:107px">SPECIAL OFFERS</a>
  <a class="active" style="width:97px">TESTIMONIALS</a>
  <a style="width:58px">BLOG</a>
  <a style="width:61px">FAQ'S</a>
  <a style="width:87px">CONTACT US</a>
</nav>

<!-- hero -->
<div class="abs hero"></div>
<div class="abs hero-photo" role="img" aria-label="Photo of a smiling couple cooking vegetables together in a home kitchen"></div>
<div class="abs hero-title">VitalPath<br>For Wellness</div>
<div class="abs hero-sub">Get the health and lifestyle<br>you want now!</div>
<div class="abs dots"><span class="on"></span><span></span><span></span><span></span></div>

<!-- breadcrumb -->
<div class="abs crumbbar"></div>
<div class="abs crumb">Home / <b>Testimonials</b></div>

<!-- title -->
<h1 class="abs section-title">Client <span>Testimonials</span></h1>
<div class="abs divider"></div>
<div class="abs divider-mark"></div>

<!-- testimonial 1 -->
<div class="abs avatar" style="left:133px;top:559px" role="img" aria-label="Portrait photo of an older smiling woman"></div>
<div class="abs avatar-tail" style="left:152px;top:630px"></div>
<div class="abs qmark qopen" style="top:555px">“</div>
<p class="abs quote" style="top:553px">"I've worked in medical research my entire adult life but always had a difficult time managing my weight. This program has taught me how to eat healthy and find an exercise routine that works for my schedule."</p>
<p class="abs body" style="top:590px">As a medical librarian in a hospital, I knew I needed to make changes to my lifestyle to stay out of the hospital as a patient—but I had a hard time actually doing it. Then I found this lifestyle change program. I was motivated to join the program to make sure I could play with my grandchildren for many years to come. I enjoy the program because I have met many people who also struggle with diet and exercise. We share healthy recipes and motivate each other to exercise. I now read food labels and ride a stationary bike for an hour a day. I am looking forward to a long, healthy life with my children and grandchildren. <span class="qmark" style="font-size:20px;vertical-align:-8px">”</span></p>
<div class="abs short-rule" style="top:684px"></div>
<div class="abs author" style="top:696px">- Marla Hensley, 60, Program Participant</div>
<div class="abs sep" style="top:728px"></div>

<!-- testimonial 2 -->
<div class="abs avatar" style="left:133px;top:760px;background:radial-gradient(circle at 50% 40%,#b58a6e,#3c2c26)" role="img" aria-label="Portrait photo of a smiling middle-aged woman"></div>
<div class="abs avatar-tail" style="left:152px;top:831px"></div>
<div class="abs qmark qopen" style="top:756px">“</div>
<p class="abs quote" style="top:754px">"Having a group of people with the same goals as me really motivated me to jump start healthy lifestyle changes."</p>
<p class="abs body" style="top:777px">After the death of my mother and a diagnosis of prediabetes, I was motivated to make healthy changes in my life to prevent type 2 diabetes. I was overweight and had high cholesterol, high glucose levels, and poor eating habits.I joined a lifestyle change program to take control of my life. During the program, I was surprised at how happy I was making healthy changes and how much I enjoyed learning from others in the group. I am now exercising regularly and learning strategies to cope with my emotional eating habits. <span class="qmark" style="font-size:20px;vertical-align:-8px">”</span></p>
<div class="abs short-rule" style="top:856px"></div>
<div class="abs author" style="top:866px">-Denise Okafor, 53, Program Participant</div>
<div class="abs sep" style="top:900px"></div>

<!-- footer -->
<footer class="abs footer"></footer>
<div class="abs f-head" style="left:131px;top:970px">QUICK <span>LINKS</span></div>
<div class="abs f-rule" style="left:131px;top:999px;width:98px"></div>
<ul class="abs links">
  <li class="current">Home</li>
  <li>About VitalPath</li>
  <li>Our Courses</li>
  <li>Special Offers</li>
  <li>Testimonials</li>
  <li>Blog</li>
  <li>Faq's</li>
  <li>Contact Us</li>
</ul>

<div class="abs f-head" style="left:265px;top:970px">CONTACT <span>DETAILS</span></div>
<div class="abs f-rule" style="left:265px;top:999px;width:160px"></div>
<div class="abs contact">
  <div class="org">VITALPATH FOR WELLNESS</div>
  123, Lorem Ipsum Dollar Smit Amet,<br>Nibh Nonumy. Golham - 123 456
  <div class="c-row"><svg width="13" height="13" viewBox="0 0 24 24"><path fill="#00a990" d="M6.6 10.8a15 15 0 0 0 6.6 6.6l2.2-2.2c.3-.3.7-.4 1-.2 1.1.4 2.3.6 3.6.6.6 0 1 .4 1 1V20c0 .6-.4 1-1 1A17 17 0 0 1 3 4c0-.6.4-1 1-1h3.5c.6 0 1 .4 1 1 0 1.3.2 2.5.6 3.6.1.3 0 .7-.2 1z"/></svg>312-555-0148</div>
  <div class="c-row"><svg width="15" height="13" viewBox="0 0 16 14"><rect x="4" y="0.5" width="8" height="4" fill="none" stroke="#00a990"/><rect x="0.5" y="4" width="15" height="6" rx="1" fill="#00a990"/><rect x="4" y="8" width="8" height="5.5" fill="#1e242d" stroke="#00a990"/></svg>312-555-0193</div>
  <div class="c-row small"><svg width="13" height="10" viewBox="0 0 13 10"><rect width="13" height="10" fill="#00a990"/><path d="M0 0l6.5 5.5L13 0" fill="none" stroke="#1e242d"/></svg>info@vitalpath4wellness.com</div>
</div>

<div class="abs f-head" style="left:461px;top:970px">FOLLOW <span>US</span></div>
<div class="abs f-rule" style="left:461px;top:999px;width:183px"></div>
<ul class="abs social" style="top:1019px">
  <li><i></i>Friendlane</li>
  <li><i></i>Chirpline</li>
  <li><i></i>Workweave</li>
  <li class="red" style="margin-top:5px"><i></i>Circleplus</li>
</ul>

<div class="abs footer-mark"></div>

<div class="abs bottom">© 2016 VitalPath For Wellness. All Rights Reserved.</div>

</body>
</html>
```